Corvane Capital Business Cards

These are professional business cards that are for my family office.
Put fake emails and phone numbers as of now until I finalize those components. This family office controls my families investments, assets, and future. The cards should be professional.
..
.
.
.
I just uploaded another variation of a logo I would like to see as a business card to I am inbeteen which logo to use

Target Market(s)

business

Industry/Entity Type

business

Contact Information for Business Card

Professional, wealth related, finance related.

Requirements
Must have
• Logo

```html
<!DOCTYPE html>
<html lang="en">
<head>
<meta charset="UTF-8">
<title>Corvane Capital Business Cards</title>
<link href="https://fonts.googleapis.com/css2?family=Cinzel:wght@700&family=Montserrat:wght@400;700&display=swap" rel="stylesheet">
<style>
  :root {
    --bg: #ececec;
    --card: #ffffff;
    --ink: #1b1d26;
    --text: #2a2a2a;
    --edge: #d9d9d9;
  }
  * { margin: 0; padding: 0; box-sizing: border-box; }
  html, body {
    width: 1200px; height: 716px; overflow: hidden;
    background: var(--bg);
  }
  .stage { position: relative; width: 1200px; height: 716px; }
  .card {
    position: absolute;
    left: 369px;
    width: 461px;
    height: 263px;
    background: var(--card);
    border-radius: 14px;
    border: 1px solid var(--edge);
  }
  .card--front { top: 95px; }
  .card--back { top: 385px; }

  .brand-name {
    font-family: "Cinzel", serif;
    font-weight: 700;
    color: var(--ink);
    white-space: nowrap;
    letter-spacing: 0.5px;
  }
  .card--front .brand-name {
    position: absolute;
    left: 0; right: 0;
    top: 112px;
    text-align: center;
    font-size: 30px;
  }
  .card--back .brand-name {
    position: absolute;
    right: 16px;
    top: 36px;
    font-size: 19px;
  }

  .contact { position: absolute; left: 18px; top: 157px; font-family: "Montserrat", sans-serif; color: var(--text); }
  .person-name { font-size: 16px; font-weight: 700; color: var(--ink); letter-spacing: 0.2px; }
  .person-role { font-size: 11.5px; margin-top: 1px; }
  .contact-list { list-style: none; margin-top: 13px; }
  .contact-item { display: flex; align-items: center; gap: 7px; font-size: 11.5px; line-height: 17px; }
  .contact-item svg { width: 11px; height: 11px; fill: var(--ink); }
</style>
</head>
<body>
<main class="stage">
  <section class="card card--front" aria-label="Card front">
    <div class="brand-name">Corvane Capital</div>
  </section>

  <section class="card card--back" aria-label="Card back">
    <div class="brand-name">Corvane Capital</div>
    <div class="contact">
      <div class="person-name">DANIEL HART</div>
      <div class="person-role">Founder</div>
      <ul class="contact-list">
        <li class="contact-item">
          <svg viewBox="0 0 12 12" aria-hidden="true"><path d="M1 4.2C1 2.6 3.4 1.8 6 1.8s5 .8 5 2.4v1H8.6V4.1C7.9 3.8 4.1 3.8 3.4 4.1v1.1H1zM3.6 5.4h4.8l2 4.6H1.6z"/></svg>
          <span>555-201-4837</span>
        </li>
        <li class="contact-item">
          <svg viewBox="0 0 12 12" aria-hidden="true"><path d="M1 2.5h10v.6L6 6.6 1 3.1zM1 4.3l5 3.5 5-3.5v5.2H1z"/></svg>
          <span>hello@corvanemail.com</span>
        </li>
      </ul>
    </div>
  </section>
</main>
</body>
</html>
```